Brisk Fixwell business card

I need business card for my business, I think you have all my details.six months ago I design with you car wrap design. We would like to design both side of the card. On front of card we would like logo , Name and our contact details.
At the back we are looking to mentioned our services.
The name will be:
Faridoullan Mestor
Managing Director
Ph:07952338417
Email:info@brisk-fixwell.com
Web:www.brisk-fixwell.com
So we have our logo, you don’t need to change the logo.
Please see the attachment.
Thanks

Target Market(s)

Home improvement

Industry/Entity Type

Home Improvement

Contact Information for Business Card

Company name: Brisk Fixwell
Name: Faridoullan Mestor
Position: Director
Ph:07952338417
Web: www.brisk-fixwell.com
Add: 42 Corvale Road
Hounslow
TW3 9KD
SECOND PERSON
Nizamuddel mestor
Position: Handyman
Ph: 07812 564037
Email: info@brisk-fixwell.com
Add: 18 Brackwin Lane Road
Hounslow
TW6 2LB

```html
<!DOCTYPE html>
<html lang="en">
<head>
<meta charset="utf-8">
<title>Brisk Fixwell – Business Card</title>
<link rel="stylesheet" href="https://fonts.googleapis.com/css2?family=Arimo:wght@400;700&display=swap">
<style>
  :root {
    --stage: #2b2b2d;
    --navy: #22387f;
    --navy-deep: #1d3072;
    --navy-light: #2c47a0;
    --red: #e11b2a;
    --ink: #4a4a4a;
    --white: #ffffff;
    --rule: #cfcfcf;
  }
  * { box-sizing: border-box; margin: 0; padding: 0; }
  html, body { width: 1200px; height: 1015px; overflow: hidden; }
  body {
    background: var(--stage);
    font-family: "Arimo", Arial, sans-serif;
    display: flex;
    flex-direction: column;
    align-items: center;
    justify-content: center;
    gap: 48px;
  }
  .card {
    width: 700px;
    height: 400px;
    position: relative;
    overflow: hidden;
    box-shadow: 0 18px 40px rgba(0,0,0,.45);
  }

  /* Back: services */
  .card--back { background: var(--navy); }
  .pattern-field {
    position: absolute; inset: 0;
    background: radial-gradient(ellipse at 70% 20%, var(--navy-light) 0%, var(--navy) 55%, var(--navy-deep) 100%);
  }
  .services {
    position: absolute;
    left: 38px; right: 30px; top: 176px;
    display: flex;
    justify-content: space-between;
  }
  .services__col { list-style: none; }
  .services__item {
    color: var(--white);
    font-size: 17px;
    line-height: 25px;
    white-space: nowrap;
    padding-left: 13px;
    position: relative;
  }
  .services__item::before {
    content: "";
    position: absolute; left: 0; top: 9px;
    width: 7px; height: 7px; border-radius: 50%;
    background: var(--red);
  }

  /* Front: identity and contacts */
  .card--front { background: var(--white); }
  .brand {
    position: absolute;
    left: 52px; top: 184px;
    display: flex; align-items: center; gap: 12px;
  }
  .brand__mark { width: 22px; height: 22px; background: var(--red); flex: none; }
  .brand__name {
    font-size: 33px; font-weight: 700; color: var(--navy);
    white-space: nowrap;
  }
  .divider {
    position: absolute; left: 360px; top: 40px; width: 1px; height: 320px;
    background: linear-gradient(to bottom, rgba(0,0,0,0), var(--rule) 30%, var(--rule) 70%, rgba(0,0,0,0));
  }
  .contact { position: absolute; left: 392px; top: 92px; }
  .contact__name {
    font-size: 21px; font-weight: 700; color: var(--navy);
    letter-spacing: .4px; text-transform: uppercase; white-space: nowrap;
  }
  .contact__role { font-size: 15px; color: var(--ink); letter-spacing: 1px; margin-bottom: 18px; text-transform: uppercase; }
  .contact__line {
    display: flex; align-items: center; gap: 10px;
    font-size: 16px; color: var(--ink); line-height: 26px; white-space: nowrap;
  }
  .contact__line svg { width: 16px; height: 16px; fill: var(--navy); flex: none; }
  .contact__line .accent { color: var(--navy); }
  .contact__address { margin-top: 16px; padding-left: 26px; font-size: 16px; line-height: 24px; color: var(--ink); }
</style>
</head>
<body>

  <section class="card card--back" aria-label="Card back: services">
    <div class="pattern-field" role="img" aria-label="Repeating embossed shield pattern in deep blue"></div>
    <div class="services">
      <ul class="services__col">
        <li class="services__item">Plumbing</li>
        <li class="services__item">Carpentry</li>
      </ul>
      <ul class="services__col">
        <li class="services__item">Decking</li>
        <li class="services__item">Fence</li>
      </ul>
      <ul class="services__col">
        <li class="services__item">Gutter</li>
        <li class="services__item">Flooring</li>
      </ul>
      <ul class="services__col">
        <li class="services__item">Plastering</li>
        <li class="services__item">Tilling</li>
      </ul>
      <ul class="services__col">
        <li class="services__item">Painting &amp; Decorating</li>
        <li class="services__item">Gardening</li>
      </ul>
    </div>
  </section>

  <section class="card card--front" aria-label="Card front: contact details">
    <div class="brand">
      <span class="brand__mark"></span>
      <span class="brand__name">Brisk Fixwell</span>
    </div>
    <div class="divider"></div>
    <div class="contact">
      <p class="contact__name">Faridoullan Mestor</p>
      <p class="contact__role">Director</p>
      <p class="contact__line">
        <svg viewBox="0 0 16 16" aria-hidden="true"><path d="M3.2 1.5l2.3 0 1.1 3.2-1.6 1.2c.8 1.8 2.2 3.2 4 4l1.2-1.6 3.2 1.1v2.3c0 .9-.8 1.6-1.7 1.5C6.4 12.7 3.3 9.6 2.8 4.3c-.1-.9.6-1.7 1.5-1.7z"/></svg>
        07952338417
      </p>
      <p class="contact__line">
        <svg viewBox="0 0 16 16" aria-hidden="true"><path d="M1 3.5h14v9H1z M1.6 4l6.4 5 6.4-5" stroke="#fff" stroke-width="1"/></svg>
        info@brisk-fixwell.com
      </p>
      <p class="contact__line">
        <svg viewBox="0 0 16 16" aria-hidden="true"><circle cx="8" cy="8" r="7"/><path d="M1 8h14M8 1c-3 3.5-3 10.5 0 14M8 1c3 3.5 3 10.5 0 14" stroke="#fff" stroke-width="1" fill="none"/></svg>
        <span>www.<span class="accent">brisk-fixwell</span>.com</span>
      </p>
      <p class="contact__address">42 Corvale Road<br>Hounslow, TW3 9KD</p>
    </div>
  </section>

</body>
</html>
```